Web and Logo Design for eCommerce site

We're launching a sister brand and require a full design for the site.

The site must have an established feel and appeal to corporate and institutional buyers.
Updates

Just a note about the wireframe design:

The Search & Rescue / Coast Guard / NVDK, etc. in the header area aren't buttons or menu items, but rather just info (along the lines of a tagline).  Sort of a "who we serve" sort of thing.

Worth noting is that it's specifically geared towards LARGE BUYERS.  For example, a police force buying 200 headlamps and 85 pairs of gloves.  So they'll register + sign in and then add a bunch of items to a RFQ.

Aim for a professional, masculine design.

Target Market(s)

We will be selling outdoor gear to the military, law enforcement, fire and rescue and first responders.

Requirements
Must have
• We require:
- Logo (vector based)

Site:
- template page
* main site template, re-skinned version of our current site
* horizontal drop-down menu
- product listings page
* thumbnail view of products
- product details page
* including elements such as product image, color/size selector, descriptions and specs (again, based loosely on our current website)
- account management page
* illustrating basic data entry styles for text box, buttons, grid, etc.

The site needs to be given a responsive design, so 2 versions of each design should be presented for desktop + mobile views.

Additional funds are available if the designer is able to fully implement the designs into a responsive framework such as bootstrap.

Nice to have
• Clean, professional design similar to:

http://military.trailvexagear.com/gov/accessories/gloves.html

http://leaf.ombrivo.com/ProductFind.aspx?language=EN&category=Hardshell&subcat=Waterproof_Jackets

```html
<!DOCTYPE html>
<html lang="en">
<head>
<meta charset="utf-8">
<title>Northvane – Canadian Outdoor Pro Supply</title>
<link href="https://fonts.googleapis.com/css2?family=Open+Sans:wght@400;600;700;800&display=swap" rel="stylesheet">
<style>
:root{
  --red:#c8191e;
  --ink:#333;
  --muted:#777;
  --line:#dcdcdc;
  --panel:#f1f1f1;
  --dark:#1e1e1e;
  --darker:#141414;
  --white:#fff;
}
*{box-sizing:border-box;margin:0;padding:0}
html,body{width:681px;height:1200px;overflow:hidden}
body{font-family:"Open Sans",Arial,sans-serif;color:var(--ink);background:#e9e9e9;font-size:8px;position:relative}
.site{position:absolute;left:0;top:0;width:681px;height:1200px;background:var(--white)}
.topbar{position:absolute;left:0;top:0;width:681px;height:64px;background:linear-gradient(#fafafa,#e6e6e6)}
.brand{position:absolute;left:62px;top:10px;display:flex;align-items:center;gap:6px}
.brand-mark{width:12px;height:12px;background:#222}
.brand-name{font-weight:700;font-size:19px;color:#222}
.brand-tag{position:absolute;left:62px;top:37px;font-size:6px;font-weight:700;color:#555;letter-spacing:.5px}
.contact{position:absolute;right:124px;top:30px;font-size:8px;color:#444}
.register{position:absolute;right:62px;top:25px;background:#222;color:#fff;font-size:8px;padding:4px 9px;border-radius:2px}
.serve{position:absolute;left:62px;top:64px;width:557px;height:20px;background:#333;display:flex;align-items:center}
.serve span{color:#ddd;font-size:7.5px;padding:0 13px;height:20px;line-height:20px}
.serve .active{background:#fff;color:#222;font-weight:700}
.login{margin-left:auto;display:flex;align-items:center;gap:6px;padding-right:5px}
.login .box{width:70px;height:12px;background:#fff;border-radius:1px;color:#888;font-size:6px;line-height:12px;padding-left:4px}
.hero{position:absolute;left:62px;top:84px;width:557px;height:226px;background:linear-gradient(135deg,#3a3a3a,#1c1c1c)}
.hero h1{position:absolute;left:20px;top:68px;color:#fff;font-size:27px;font-weight:400;line-height:1.2;width:280px}
.hero p{position:absolute;left:20px;top:144px;width:230px;color:#bbb;font-size:6.5px;line-height:1.4}
.hero .more{position:absolute;left:20px;top:176px;color:var(--red);font-size:7px}
.hero-gear{position:absolute;left:270px;top:12px;width:270px;height:200px;border-radius:3px;background:radial-gradient(circle at 50% 45%,#8a7a55,#5a4d35 55%,#2b2b2b)}
.sidebar{position:absolute;left:62px;top:342px;width:170px}
.side-title{font-size:15px;color:#555;margin-bottom:8px}
.cats{background:var(--panel);list-style:none;padding:6px 0}
.cats li{font-size:7px;padding:6px 10px 6px 24px;position:relative;color:#333}
.cats li::before{content:"";position:absolute;left:12px;top:9px;border-left:4px solid #333;border-top:3px solid transparent;border-bottom:3px solid transparent}
.best{position:absolute;left:62px;top:706px;width:170px}
.best-item{display:flex;gap:8px;margin-bottom:14px}
.best-thumb{width:40px;height:40px;border-radius:50%;background:radial-gradient(#7a7050,#4b4633)}
.best-info{font-size:7px;line-height:1.35}
.best-info b{display:block}
.stars{color:var(--red);letter-spacing:1px}
.account{margin-top:10px;background:var(--panel);padding:12px;text-align:center}
.account h4{font-size:8px;margin-bottom:6px}
.account p{font-size:6.5px;color:var(--muted);line-height:1.4;margin-bottom:8px}
.account .btn{display:inline-block;border:1px solid #bbb;background:#fff;font-size:7px;padding:3px 14px}
.section{position:absolute;left:252px;width:367px}
.latest{top:342px}
.featured{top:706px}
.sec-head{display:flex;justify-content:space-between;align-items:center;margin-bottom:8px}
.sec-head h2{font-size:15px;font-weight:400;color:#555}
.view{background:#777;color:#fff;font-size:6px;padding:2px 6px;border-radius:2px}
.cards{display:flex;gap:14px}
.card{background:#fff;border:1px solid var(--line);box-shadow:0 1px 3px rgba(0,0,0,.15);padding:8px;flex:1}
.card .img{height:100px;background:linear-gradient(#f4f4f4,#e4e2dc)}
.latest .card .img{height:118px}
.row{display:flex;justify-content:space-between;align-items:center;margin-top:8px;font-size:7px}
.cart{border:1px solid #bbb;font-size:6px;padding:2px 5px;border-radius:2px}
.card h3{font-size:7.5px;font-weight:400;margin-top:8px}
.card p{font-size:6px;color:var(--muted);line-height:1.4;margin-top:4px}
.card .dealer{color:var(--red);font-size:6px;margin-top:6px}
.footer{position:absolute;left:62px;top:1010px;width:557px;height:152px;background:var(--dark)}
.guarantee{position:absolute;left:22px;top:20px;color:var(--red);font-weight:800;font-size:14px;line-height:1.15}
.fcol{position:absolute;top:22px;color:#aaa;font-size:6px;line-height:1.7}
.fcol h5{color:#fff;font-size:7px;margin-bottom:4px}
.soc{display:flex;align-items:center;gap:5px;margin-bottom:3px}
.soc i{width:9px;height:9px;border-radius:50%;background:#555;display:inline-block}
.copy{position:absolute;left:62px;top:1162px;width:557px;height:22px;background:var(--darker);color:#aaa;font-size:6.5px;text-align:center;line-height:22px}
</style>
</head>
<body>
<div class="site">
  <header class="topbar">
    <div class="brand"><span class="brand-mark"></span><span class="brand-name">Northvane</span></div>
    <div class="brand-tag">CANADIAN OUTDOOR PRO SUPPLY</div>
    <div class="contact">Contact Us | 123-456-7890</div>
    <div class="register">Register</div>
  </header>
  <nav class="serve">
    <span class="active">Search &amp; Rescue</span><span>Coast Guard</span><span>NVDK</span><span>Fire</span><span>Military</span><span>Law Enforcement</span>
    <div class="login"><span style="color:#ddd;font-size:7px">Login</span><span class="box">Search…</span></div>
  </nav>
  <section class="hero">
    <h1>Canadian Outdoor Pro Supply</h1>
    <p>Durable field gear for rescue teams, police forces and military units, supplied in bulk with reliable quotes and fast delivery across Canada every season.</p>
    <div class="more">» View Products</div>
    <div class="hero-gear" role="img" aria-label="Tactical vest, gloves, boots and belt gear"></div>
  </section>

  <aside class="sidebar">
    <div class="side-title">Product Categories</div>
    <ul class="cats">
      <li>Clearance</li><li>Field Gear</li><li>Tactical Bags</li><li>Surplus Gear</li><li>Military Clothing Surplus</li><li>Camping Gear</li><li>Snow Sports</li><li>Fire</li><li>NVDK</li><li>Footwear</li><li>Law Enforcement</li><li>Field Gear</li>
    </ul>
  </aside>

  <section class="section latest">
    <div class="sec-head"><h2>Latest Products</h2><span class="view">View all</span></div>
    <div class="cards">
      <article class="card">
        <div class="img" role="img" aria-label="Olive survival kit pouch"></div>
        <div class="row"><span>$ 1,599.00</span><span class="cart">Add to cart</span></div>
        <h3>Survival Kit</h3>
        <p>Compact kit with essentials for field crews, sealed and ready for bulk orders.</p>
        <div class="dealer">» Dealers</div>
      </article>
      <article class="card">
        <div class="img" role="img" aria-label="Lensatic compass"></div>
        <div class="row"><span>$ 1,599.00</span><span class="cart">Add to cart</span></div>
        <h3>Lensatic Compass</h3>
        <p>Rugged sighting compass built for navigation in harsh terrain and low light.</p>
        <div class="dealer">» Dealers</div>
      </article>
    </div>
  </section>

  <aside class="best">
    <div class="side-title">Best Sellers</div>
    <div class="best-item"><div class="best-thumb" role="img" aria-label="Best seller product"></div><div class="best-info"><b>New Product</b>Please enter name here<br>$ 99.00<br><span class="stars">★★★★★</span></div></div>
    <div class="best-item"><div class="best-thumb" role="img" aria-label="Best seller product"></div><div class="best-info"><b>New Product</b>Please enter name here<br>$ 99.00<br><span class="stars">★★★★★</span></div></div>
    <div class="account">
      <h4>Create your account for FREE!</h4>
      <p>Register your agency to build quotes, track orders and save item lists.</p>
      <span class="btn">Sign Up</span>
    </div>
  </aside>

  <section class="section featured">
    <div class="sec-head"><h2>Featured Products</h2><span class="view">View all</span></div>
    <div class="cards">
      <article class="card">
        <div class="img" role="img" aria-label="Olive tactical vest"></div>
        <div class="row"><span>$ 299.00</span></div>
        <h3>Modular Tactical System</h3>
        <p>Adjustable carrier with modular loops for mission-ready loadouts.</p>
        <div class="row"><span class="dealer" style="margin:0">» Dealers</span><span class="cart">Add to cart</span></div>
      </article>
      <article class="card">
        <div class="img" role="img" aria-label="Dark green military jacket"></div>
        <div class="row"><span>$ 299.00</span></div>
        <h3>Military Over Coat</h3>
        <p>Insulated weatherproof coat for long shifts in cold conditions.</p>
        <div class="row"><span class="dealer" style="margin:0">» Dealers</span><span class="cart">Add to cart</span></div>
      </article>
      <article class="card">
        <div class="img" role="img" aria-label="Red tent and sleeping bag"></div>
        <div class="row"><span>$ 299.00</span></div>
        <h3>Tent + 3 Sleeping Bags</h3>
        <p>Shelter bundle sized for small teams on extended deployments.</p>
        <div class="row"><span class="dealer" style="margin:0">» Dealers</span><span class="cart">Add to cart</span></div>
      </article>
    </div>
  </section>

  <footer class="footer">
    <div class="guarantee">GET YOUR<br>NORTHVANE<br>LIFE TIME<br>GUARANTEE</div>
    <div class="fcol" style="left:185px"><h5>CUSTOMER SERVICE</h5>My Account<br>Product Care<br>Warranty<br>Order Status<br>Shipping Info<br>Easy Returns<br>Shipping Policy</div>
    <div class="fcol" style="left:300px"><h5>ABOUT NORTHVANE</h5>Our Story<br>Work Here<br>Social Responsibility<br>Supply Contracts<br>Press<br>Contact<br>Sitemap</div>
    <div class="fcol" style="left:430px"><h5>CONNECT</h5>
      <div class="soc"><i></i>Friendlink</div>
      <div class="soc"><i></i>Chirpline</div>
      <div class="soc"><i></i>Pinboard</div>
    </div>
  </footer>
  <div class="copy">© northvane.com – All Rights Reserved</div>
</div>
</body>
</html>
```